Mobile Fitness snd Therapy Business Card Design

I need a business card designed for my mobile fitness and therapy business.

Please view the images that I have uploaded. I like the simplicity of the design that I have attached. I adapted it with my information

Target Market(s)

Those seeking personal training, injury rehabilitation or massage therapy.

Industry/Entity Type

Business

Contact Information for Business Card

Derek Fulham - MSc, CAT(C), RMT, CSCS, Pn2
e-mail: derek@vantrelo.com
website: www.vantrelo.com
instagram: @derek_fulham

Font styles to use
Sans Serif

Colors
3176b5
0355a3

Requirements
Must have
• "Contact us to receive a FREE assessment"
• Services offered:
• Personal Training
• Golf Fitness
• Injury Rehab
• Massage Therapy
• Yoga
Nice to have
• Consistent colours with brand
• - Dark Blue: #232837
• - Blue: #5096f0
• Consistent look/feel with the website: www.vantrelo.com

```html
<!DOCTYPE html>
<html lang="en">
<head>
<meta charset="utf-8">
<title>Vantrelo Business Card</title>
<link rel="stylesheet" href="https://fonts.googleapis.com/css2?family=Roboto:wght@400;500;700;900&family=Roboto+Condensed:wght@700&display=swap">
<style>
  :root {
    --bg: #e9e9ea;
    --card-light: #f4f4f4;
    --card-dark: #222839;
    --ink-dark: #232837;
    --brand-blue: #2f5fd6;
    --text-grey: #555a63;
    --white: #ffffff;
    --divider: #5f7fc4;
  }
  * { margin: 0; padding: 0; box-sizing: border-box; }
  html, body { width: 1200px; height: 960px; overflow: hidden; }
  body { background: var(--bg); font-family: "Roboto", sans-serif; position: relative; }

  .card {
    position: absolute;
    width: 600px;
    height: 343px;
    border-radius: 22px;
  }
  .card--front { left: 314px; top: 113px; background: var(--card-light); }
  .card--back { left: 311px; top: 472px; background: var(--card-dark); }

  .wordmark {
    position: absolute;
    font-family: "Roboto", sans-serif;
    font-weight: 700;
    font-size: 48px;
    line-height: 1;
    letter-spacing: 4px;
    text-align: center;
  }
  .tagline {
    position: absolute;
    font-family: "Roboto", sans-serif;
    font-weight: 700;
    font-size: 14px;
    letter-spacing: 2.4px;
    text-align: center;
    white-space: nowrap;
  }
  .card--front .wordmark { left: 76px; top: 92px; width: 306px; color: var(--ink-dark); }
  .card--front .tagline { left: 76px; top: 137px; width: 306px; color: var(--ink-dark); }

  .holder { position: absolute; left: 76px; top: 207px; }
  .holder__name {
    font-family: "Roboto Condensed", sans-serif;
    font-weight: 700;
    font-size: 22px;
    color: var(--brand-blue);
    text-transform: uppercase;
    line-height: 1;
  }
  .holder__credentials {
    margin-top: 4px;
    font-family: "Roboto Condensed", sans-serif;
    font-weight: 700;
    font-size: 10.5px;
    color: var(--brand-blue);
  }

  .contact { position: absolute; left: 273px; top: 198px; list-style: none; }
  .contact__item {
    display: flex; align-items: center; gap: 8px;
    height: 19px;
    font-size: 14px; color: var(--text-grey);
  }
  .contact__icon { width: 14px; height: 14px; flex: none; }

  .card--back .wordmark { left: 120px; top: 130px; width: 360px; color: var(--white); }
  .card--back .tagline { left: 120px; top: 180px; width: 360px; color: var(--white); font-size: 15px; }

  .offer {
    position: absolute; left: 58px; top: 258px;
    width: 484px; height: 33px;
    border-radius: 17px;
    background: var(--brand-blue);
    color: var(--white);
    font-family: "Roboto Condensed", sans-serif;
    font-weight: 700; font-size: 20px;
    text-transform: uppercase;
    display: flex; align-items: center; justify-content: center;
  }
  .services {
    position: absolute; left: 0; top: 297px; width: 600px;
    list-style: none;
    display: flex; justify-content: center;
    font-size: 14.5px; color: var(--white);
  }
  .services__item + .services__item::before {
    content: "|"; color: var(--divider); margin: 0 5px;
  }
</style>
</head>
<body>

<section class="card card--front" aria-label="Business card front">
  <div class="wordmark">VANTRELO</div>
  <div class="tagline">NUTRITION - FITNESS - HEALTH</div>

  <div class="holder">
    <div class="holder__name">Derek Fulham</div>
    <div class="holder__credentials">MSC, CAT(C), RMT, CSCS, PN2</div>
  </div>

  <ul class="contact">
    <li class="contact__item">
      <svg class="contact__icon" viewBox="0 0 14 14" aria-hidden="true">
        <rect x="1" y="3" width="12" height="8" rx="1" fill="var(--brand-blue)"/>
        <path d="M1.5 3.5 L7 7.5 L12.5 3.5" fill="none" stroke="var(--card-light)" stroke-width="1.2"/>
      </svg>
      derek@vantrelo.com
    </li>
    <li class="contact__item">
      <svg class="contact__icon" viewBox="0 0 14 14" aria-hidden="true">
        <circle cx="7" cy="7" r="6" fill="var(--brand-blue)"/>
        <path d="M1 7 H13 M7 1 C4 4 4 10 7 13 M7 1 C10 4 10 10 7 13" fill="none" stroke="var(--card-light)" stroke-width="1"/>
      </svg>
      www.vantrelo.com
    </li>
    <li class="contact__item">
      <svg class="contact__icon" viewBox="0 0 14 14" aria-hidden="true">
        <circle cx="7" cy="7" r="6" fill="var(--brand-blue)"/>
      </svg>
      @derek_fulham
    </li>
  </ul>
</section>

<section class="card card--back" aria-label="Business card back">
  <div class="wordmark">VANTRELO</div>
  <div class="tagline">NUTRITION - FITNESS - HEALTH</div>

  <div class="offer">Contact us to receive a free assessment</div>
  <ul class="services">
    <li class="services__item">Personal Training</li>
    <li class="services__item">Golf Fitness</li>
    <li class="services__item">Injury Rehab</li>
    <li class="services__item">Massage Therapy</li>
    <li class="services__item">Yoga</li>
  </ul>
</section>

</body>
</html>
```